Tjirpsa car advertisement

de website moet uit minimaal 3 pagina's bestaan. 1 pagina als een landingspagina. 1 pagina voor consumenten die hun auto willen laten beplakken met bedrijfsreclame en 1 pagina voor bedrijven / consumenten die hun bedrijfsreclame op een consumentenauto wilt plaatsen.

de website moet echt een happy website zijn. consumenten kunnen geld verdienen met reclame op hun auto te laten zetten en bedrijven kunnen voor een relatief goedkoop bedrag hun bedrijfsreclame op een auto laten zetten. die auto rijdt dan rond en veel mensen zien de reclame.

beide pagina's moeten dus een glimlach opleveren.

het doel van de startpagina is dat je door kunt gaan naar de consumenten en de bedrijfspagina.

gebruik leuke, vrolijke kleuren en vormen en zorg dat de mensen een glimlach krijgen als ze naar de website kijken.

doelgroep is consumenten die een auto rijden en geld willen verdienen met hun auto en de zakelijke ondernemer die voor een goedkoop bedrag zijn bedrijfsreclame met een full carwrap kan laten zien aan de buitenwereld.

doordat consumenten zich bij ons aanmelden hebben wij een database met auto's en weten we hoeveel deze auto's rijden en in welke regio's ze rijden en wat voor auto ze rijden. allemaal hele belangrijke informatie voor een ondernemer die reclame wilt maken op ene specifieke auto type en in een bepaalde regio.

-

website should consist of at least 3 pages. 1 landing page, 1 customer page and 1 business page. landing page let's the visitor choose wether he / she is a customer with a car and wants to allow his car to be fully carwrapped or he / she is a business owner who wants to place his advertisement on a car.

website should be a really happy joyfull website and bring a smile to the visitor. beause the customer can earn money (200 euro / month nett) by allowing advertisements on his car (full car wrap) and the business owner because for a low price he can advertise.

when customers that owns a car register themselves with our website we build a database with cars in specific locations. a business owner wants to advertise his product into a specific region. this is very valuable information.

agreement is 1 year for a customer to have advertisements on his car and for a business to advertise. after that year, the advertisements are safely removed from the car and new advertisement agreements can be made. a business can place advertisements (full carwrap) already for 795 euro's., Details for my new Web Design Project will be added soon. , de website moet uit minimaal 3 pagina's bestaan. 1 pagina als een landingspagina. 1 pagina voor consumenten die hun auto willen laten beplakken met bedrijfsreclame en 1 pagina voor bedrijven / consumenten die hun bedrijfsreclame op een consumentenauto wilt plaatsen.

Target Market(s)

customers who has a car
businesses who want to advertise their business / product on a car

Industry/Entity Type

Business

Requirements
Must have
• website should be playfull, colorfull and a joy to look at and work with. altough functoinality is very limited visitors need to be intrigued to proceed to contact tjirpsa.
Nice to have
• nice graphics, moving images, a "living" website (not so static)

```html
<!DOCTYPE html>
<html lang="en">
<head>
<meta charset="utf-8">
<title>Tjirpsa Car</title>
<link href="https://fonts.googleapis.com/css2?family=Open+Sans:wght@400;600;700&display=swap" rel="stylesheet">
<style>
:root{
  --navy:#0d2748;
  --navy-2:#16386228;
  --nav:#1f5f9e;
  --blue:#1c8bd4;
  --blue-light:#3ea8ea;
  --band:#edf1f5;
  --text:#4a4f55;
  --muted:#7a8088;
  --footer:#2a2c2f;
  --footer-2:#1f2123;
  --white:#ffffff;
}
*{box-sizing:border-box;margin:0;padding:0}
html,body{width:779px;height:1200px;overflow:hidden;background:var(--white)}
body{font-family:"Open Sans",Arial,sans-serif;color:var(--text);font-size:9px;line-height:1.45;position:relative}
.header{position:absolute;top:0;left:0;width:779px;height:80px;background:linear-gradient(#0b213d,#143a66)}
.brand{position:absolute;left:38px;top:12px;display:flex;align-items:center;gap:8px}
.brand-dot{width:22px;height:22px;border-radius:50%;background:var(--blue-light)}
.brand-name{color:var(--white);font-weight:700;font-size:17px;letter-spacing:.5px}
.top-tools{position:absolute;right:38px;top:12px;display:flex;align-items:center;gap:6px;color:#cfe1f3;font-size:8px}
.social-dot{width:12px;height:12px;border-radius:50%;background:#3d6fa3}
.tool-btn{border:1px solid #5d8cbc;color:var(--white);padding:2px 7px;margin-left:4px;font-size:8px}
.nav{position:absolute;top:52px;left:0;width:779px;height:28px;display:flex;padding-left:38px}
.nav a{color:var(--white);text-decoration:none;font-size:9.5px;font-weight:600;padding:0 15px;line-height:28px;border-right:1px solid #2d5787}
.nav a:first-child{padding-left:4px}
.hero{position:absolute;top:80px;left:78px;width:623px;height:272px;background:linear-gradient(160deg,#8fb6c9 0%,#c6d7d0 35%,#e8ecef 55%,#5f7d55 80%,#4b6345 100%)}
.hero-arrow{position:absolute;top:198px;width:28px;height:28px;border-radius:50%;background:var(--white);box-shadow:0 1px 4px rgba(0,0,0,.35);display:flex;align-items:center;justify-content:center}
.caption{position:absolute;top:357px;left:78px;width:623px;height:40px;background:var(--blue);border-radius:4px;display:flex;align-items:center;padding:0 12px;color:var(--white);font-size:8px;gap:20px}
.caption p{flex:1}
.btn{background:var(--blue);color:var(--white);font-size:8px;padding:3px 10px;display:inline-block;border-radius:2px;text-align:center}
.caption .btn{background:#0f6fb2;padding:5px 18px;font-size:9px}
.steps{position:absolute;top:403px;left:0;width:779px;height:236px;background:var(--band);display:flex;justify-content:center;gap:22px;padding-top:20px}
.step{width:118px;text-align:center;position:relative}
.step-circle{width:76px;height:76px;border-radius:50%;background:#dfe5eb;border:3px solid var(--white);margin:0 auto;display:flex;align-items:center;justify-content:center;box-shadow:0 1px 3px rgba(0,0,0,.15)}
.step h3{font-size:10.5px;color:#1d2b3a;margin:8px 0 5px;font-weight:700;line-height:1.2}
.step p{font-size:7.5px;color:var(--muted);height:42px}
.step .btn{width:100%;margin-top:6px;padding:4px 0}
.step-arrow{position:absolute;right:-22px;top:28px}
.news{position:absolute;top:651px;left:30px;width:719px;height:128px;display:flex;gap:12px}
.news-text{width:300px}
.news-text h2{color:var(--blue);font-size:11px;font-weight:600;margin-bottom:5px}
.news-text p{font-size:8px;color:var(--muted)}
.news-meta{display:flex;align-items:center;gap:10px;margin-top:8px;font-size:8px}
.news-meta .btn{padding:3px 22px}
.photo{flex:1;height:124px}
.p1{background:linear-gradient(135deg,#7aa0c2,#cfd9e2 60%,#52616e)}
.p2{background:linear-gradient(135deg,#9aa9b6,#e4e7ea 50%,#6b7886)}
.p3{background:linear-gradient(135deg,#b7c7d4,#f1f3f5 45%,#8a99a6)}
.divider{position:absolute;top:790px;left:30px;width:719px;height:1px;background:#d5dbe1}
.services{position:absolute;top:800px;left:30px;width:285px}
.about{position:absolute;top:800px;left:330px;width:419px}
.section-title{color:var(--blue);font-size:13px;font-weight:700;border-bottom:1px solid #d5dbe1;padding-bottom:3px;margin-bottom:8px}
.service-list{display:grid;grid-template-columns:1fr 1fr;column-gap:12px;list-style:none}
.service-list li{font-size:8px;color:var(--text);padding:4px 0 4px 12px;border-bottom:1px dotted #d0d6dc;position:relative}
.service-list li::before{content:"›";position:absolute;left:2px;top:1px;color:var(--blue);font-size:11px;font-weight:700}
.about p{font-size:8px;color:var(--muted);margin-bottom:7px}
.about-social{display:flex;gap:6px;margin-top:4px}
.about-social span{width:18px;height:18px;border-radius:50%;background:var(--blue)}
.footer{position:absolute;top:983px;left:0;width:779px;height:217px;background:var(--footer);color:#c7cacd;display:flex;padding:16px 30px 0;gap:20px}
.footer h4{color:var(--white);font-size:13px;font-weight:600;margin-bottom:8px}
.f-brand{width:170px}
.f-brand p{font-size:7.5px;color:#a6aaae}
.f-social{display:flex;gap:5px;margin-top:10px}
.f-social span{width:16px;height:16px;border-radius:50%;background:#4a4e53}
.f-testi{width:300px;border-left:1px solid #3d4044;border-right:1px solid #3d4044;padding:0 16px}
.f-testi ul{list-style:none}
.f-testi li{font-size:7.5px;color:#a6aaae;padding-left:14px;position:relative;margin-bottom:10px}
.f-testi li::before{content:"›";position:absolute;left:0;top:-3px;color:var(--white);font-size:14px}
.f-contact{flex:1}
.field{display:flex;align-items:center;margin-bottom:5px;font-size:7.5px}
.field label{width:52px}
.field span{flex:1;height:13px;background:var(--white)}
.field.msg span{height:34px}
.f-contact .btn{float:right;padding:3px 14px;margin-top:2px}
.footer-bottom{position:absolute;left:0;bottom:0;width:779px;height:16px;background:var(--footer-2)}
</style>
</head>
<body>
<header class="header">
  <div class="brand"><span class="brand-dot"></span><span class="brand-name">TJIRPSA CAR</span></div>
  <div class="top-tools">Follow us:
    <span class="social-dot"></span><span class="social-dot"></span><span class="social-dot"></span><span class="social-dot"></span>
    <span class="tool-btn">Login</span><span class="tool-btn">Sign up</span>
  </div>
  <nav class="nav"><a>Home</a><a>About Us</a><a>Our Services</a><a>Our News</a><a>Contact Us</a></nav>
</header>

<div class="hero" role="img" aria-label="Photo of a small hatchback with a full advertising car wrap parked on a street"></div>
<div class="hero-arrow" style="left:64px"><svg width="12" height="12" viewBox="0 0 12 12"><path d="M8 1 3 6l5 5" stroke="#333" stroke-width="2" fill="none"/></svg></div>
<div class="hero-arrow" style="left:687px"><svg width="12" height="12" viewBox="0 0 12 12"><path d="M4 1l5 5-5 5" stroke="#333" stroke-width="2" fill="none"/></svg></div>

<div class="caption">
  <p>Lorem ipsum dolor sit amet lorem ipsum dolor sit amet lorem ipsum dolor sit amet lorem ipsum dolor sit amet<br>lorem ipsum dolor sit amet lorem ipsum dolor sit amet lorem ipsum dolor.</p>
  <span class="btn">More information</span>
</div>

<section class="steps">
  <div class="step">
    <div class="step-circle"><svg width="36" height="36" viewBox="0 0 36 36"><circle cx="15" cy="15" r="9" stroke="#1d2b3a" stroke-width="4" fill="none"/><path d="M22 22l9 9" stroke="#1d2b3a" stroke-width="5" stroke-linecap="round"/></svg></div>
    <h3>Find Car</h3>
    <p>We help you find the right car near you, in the region and type you want.</p>
    <span class="btn">More information</span>
    <svg class="step-arrow" width="14" height="20" viewBox="0 0 14 20"><path d="M2 2l9 8-9 8" stroke="#1c8bd4" stroke-width="3" fill="none"/></svg>
  </div>
  <div class="step">
    <div class="step-circle"><svg width="36" height="36" viewBox="0 0 36 36"><circle cx="18" cy="11" r="7" fill="#1d2b3a"/><path d="M5 33c0-9 6-13 13-13s13 4 13 13z" fill="#1d2b3a"/></svg></div>
    <h3>Car Owner</h3>
    <p>Car owners sign up with their car, region and the distance they drive.</p>
    <span class="btn">More information</span>
    <svg class="step-arrow" width="14" height="20" viewBox="0 0 14 20"><path d="M2 2l9 8-9 8" stroke="#1c8bd4" stroke-width="3" fill="none"/></svg>
  </div>
  <div class="step">
    <div class="step-circle"><svg width="42" height="24" viewBox="0 0 42 24"><path d="M3 17v-5l6-2 6-6h13l7 6 5 2v5z" fill="#1d2b3a"/><circle cx="11" cy="18" r="4" fill="#dfe5eb" stroke="#1d2b3a" stroke-width="2"/><circle cx="31" cy="18" r="4" fill="#dfe5eb" stroke="#1d2b3a" stroke-width="2"/></svg></div>
    <h3>Car Wrap<br>Advertisement</h3>
    <p>A full car wrap with your business ad, seen by many people every day.</p>
    <span class="btn">More information</span>
    <svg class="step-arrow" width="14" height="20" viewBox="0 0 14 20"><path d="M2 2l9 8-9 8" stroke="#1c8bd4" stroke-width="3" fill="none"/></svg>
  </div>
  <div class="step">
    <div class="step-circle"><svg width="40" height="40" viewBox="0 0 40 40"><circle cx="20" cy="20" r="17" fill="#1d2b3a"/><text x="20" y="19" fill="#fff" font-family="Open Sans, sans-serif" font-size="9" font-weight="700" text-anchor="middle">200</text><text x="20" y="28" fill="#fff" font-family="Open Sans, sans-serif" font-size="6" text-anchor="middle">EURO</text></svg></div>
    <h3>Car Owner<br>get 200 Euro</h3>
    <p>Car owners earn 200 euro net each month for one full year.</p>
    <span class="btn">More information</span>
    <svg class="step-arrow" width="14" height="20" viewBox="0 0 14 20"><path d="M2 2l9 8-9 8" stroke="#1c8bd4" stroke-width="3" fill="none"/></svg>
  </div>
  <div class="step">
    <div class="step-circle"><svg width="34" height="36" viewBox="0 0 34 36"><path d="M6 3v31" stroke="#1d2b3a" stroke-width="3"/><path d="M7 4h22l-5 7 5 7H7z" fill="#1d2b3a"/></svg></div>
    <h3>Finish</h3>
    <p>After one year the wrap is safely removed and a new deal can start.</p>
    <span class="btn">More information</span>
  </div>
</section>

<section class="news">
  <div class="news-text">
    <h2>Car Advertisement - Los Angeles January</h2>
    <p>Vivamus sagittis lacus vel augue laoreet rutrum faucibus dolor auctor. Fusce dapibus, tellus ac cursus commodo, tortor mauris condimentum nibh, ut fermentum massa justo sit amet risus. Fusce dapibus, tellus ac cursus commodo, tortor mauris nibh.</p>
    <div class="news-meta"><span>20.01.2015</span><span class="btn">Details</span></div>
  </div>
  <div class="photo p1" role="img" aria-label="Photo of a wrapped car parked outside"></div>
  <div class="photo p2" role="img" aria-label="Photo of a car wrap being applied in a workshop"></div>
  <div class="photo p3" role="img" aria-label="Photo of a finished advertising car wrap"></div>
</section>

<div class="divider"></div>

<section class="services">
  <h2 class="section-title">Services:</h2>
  <ul class="service-list">
    <li>Donec sed odio consectetur</li><li>Cras justo odio consectetur</li>
    <li>Purus sit amet fermentum</li><li>Purus sit amet fermentum</li>
    <li>Duis mollis, est non</li><li>Duis mollis, est non</li>
    <li>Maeb luctus, nisi erat porttitor</li><li>Maeb luctus, nisi erat</li>
    <li>Tur ligula, eget lacinia odio</li><li>Tur ligula, eget lacinia</li>
    <li>Sem nec elit. Maecenas</li><li>Sem nec elit. Maecenas</li>
    <li>Faucibus mollis interdum</li><li>Faucibus mollis interdum</li>
  </ul>
</section>

<section class="about">
  <h2 class="section-title">About us:</h2>
  <p>Maecenas faucibus mollis interdum. Nullam id dolor id nibh ultricies vehicula ut id elit. Vestibulum id ligula porta felis euismod semper. Cras mattis consectetur purus sit amet fermentum. Cras justo odio, dapibus ac facilisis in, egestas eget quam.</p>
  <p>Donec sed odio dui. Morbi risus, porta ac consectetur ac, vestibulum at eros. Aenean eu leo quam. Pellentesque ornare sem lacinia quam venenatis vestibulum. Integer posuere erat a ante venenatis dapibus posuere velit aliquet.</p>
  <p>Donec sed odio dui. Morbi leo risus, porta ac consectetur ac, vestibulum at eros. Aenean eu leo quam. Pellentesque ornare sem lacinia quam venenatis.</p>
  <div class="about-social"><span></span><span></span><span></span><span></span><span></span></div>
</section>

<footer class="footer">
  <div class="f-brand">
    <h4>Brightlane</h4>
    <p>Nullam quis risus eget urna mollis ornare vel eu leo. Cum sociis natoque penatibus et magnis dis parturient montes, nascetur ridiculus mus. Donec ullamcorper nulla non metus auctor fringilla.</p>
    <div class="f-social"><span></span><span></span><span></span></div>
  </div>
  <div class="f-testi">
    <h4>Testimonials:</h4>
    <ul>
      <li>Maecenas faucibus mollis interdum. Morbi leo risus, porta ac consectetur ac, vestibulum at eros. Donec sed odio dui.</li>
      <li>Maecenas faucibus mollis interdum. Morbi leo risus, porta ac consectetur ac, vestibulum at eros. Donec sed odio dui.</li>
      <li>Maecenas faucibus mollis interdum. Morbi leo risus, porta ac consectetur ac, vestibulum at eros. Donec sed odio dui.</li>
    </ul>
  </div>
  <div class="f-contact">
    <h4>Contact us:</h4>
    <div class="field"><label>Your name</label><span></span></div>
    <div class="field"><label>Your e-mail</label><span></span></div>
    <div class="field msg"><label>Message</label><span></span></div>
    <span class="btn">Send</span>
  </div>
  <div class="footer-bottom"></div>
</footer>
</body>
</html>
```